Super Greens Label for Supplement Bottle

We want to design a front label for a health supplement bottle. The product is called Meadow Crunch Chews™. This will be a new product so there is no current website for the product. The focus is on supergreens that taste great and deliver support for energy, digestion, and immune defense.
We want it to be modern, vibrant and appealing.
Bottle size: standard size supplement CLEAR bottle size, with white child resistant cap and the label panel dimensions are 3” x 7”. The label should be primarily white and green, with a touch of red; (see color palettes)/it can also ONLY be white and green. See samples attached.
We are only focused on the front of the bottle design, not on the back, but leave space for the supplement panel and other text on the back.
So the text for the front of the bottle is:
RT Halvorsen's
Meadow Crunch Chews™
Super Greens Blend for:
Energy, Digestion, and Immune Support*
60 Gummies | Dietary Supplement
Raspberry Flavor Gummies
Off to side of the label:
Non-GMO
Vegan Friendly
Plant-Based
Gelatin Free
Colors
Designer to choose colors to be used in the design.
Look and feel
Each slider illustrates characteristics of the customer's brand and the style your logo design should communicate.

```html
<!DOCTYPE html>
<html lang="en">
<head>
<meta charset="utf-8">
<title>Meadow Crunch Chews – Front Label</title>
<link rel="stylesheet" href="https://fonts.googleapis.com/css2?family=Montserrat:wght@600;700;800&family=Barlow+Semi+Condensed:wght@300;400;500;600&display=swap">
<style>
  :root{
    --green-dark:#2f6e37;
    --green-mid:#3f8a45;
    --green-pill:#62bd66;
    --green-pale:#dcebd9;
    --ink:#2a2a2a;
    --white:#ffffff;
    --page:#eef1ee;
  }
  *{margin:0;padding:0;box-sizing:border-box}
  html,body{width:1200px;height:1200px;overflow:hidden;background:var(--page)}
  .label{
    position:absolute;left:175px;top:53px;width:850px;height:1094px;
    background:linear-gradient(180deg,var(--white) 0%,var(--white) 55%,var(--green-pale) 80%);
    overflow:hidden;
    font-family:"Barlow Semi Condensed",sans-serif;
  }
  .band-top{position:absolute;left:0;top:0;width:100%;height:38px;background:var(--green-dark)}
  .count-tab{
    position:absolute;left:0;top:38px;width:82px;height:178px;
    background:var(--green-dark);border-radius:0 0 26px 0;
    color:var(--white);text-align:center;padding-top:28px;
  }
  .count-tab .num{font-family:"Montserrat",sans-serif;font-weight:800;font-size:56px;line-height:1}
  .count-tab .unit{font-family:"Montserrat",sans-serif;font-weight:700;font-size:13px;letter-spacing:-.3px;margin-top:8px}
  .leaf-spray{position:absolute;left:600px;top:20px;width:140px;height:160px;
    background:radial-gradient(ellipse at 55% 45%,#3d8f3a 0%,#6cb84f 55%,rgba(108,184,79,0) 75%)}
  .brand{position:absolute;left:0;width:770px;top:110px;text-align:center;white-space:nowrap;
    font-family:"Montserrat",sans-serif;font-weight:700;font-size:40px;color:var(--ink);letter-spacing:.5px}
  .title{position:absolute;left:82px;width:670px;text-align:center;white-space:nowrap;font-family:"Montserrat",sans-serif;color:var(--green-dark);line-height:1}
  .title-main{top:228px;font-weight:800;font-size:62px;letter-spacing:-1px}
  .title-sub{top:318px;font-weight:700;font-size:64px;letter-spacing:9px}
  .blend-pill{position:absolute;left:124px;top:437px;width:600px;height:88px;border-radius:44px;
    background:var(--green-pill);color:var(--white);font-weight:500;font-size:44px;white-space:nowrap;
    display:flex;align-items:center;justify-content:center;letter-spacing:-.5px}
  .benefit{position:absolute;left:0;width:850px;padding-right:80px;text-align:center;color:var(--ink);letter-spacing:-1px;white-space:nowrap}
  .benefit-main{top:562px;font-weight:600;font-size:66px}
  .benefit-sub{top:662px;font-weight:500;font-size:52px}
  .supplement{position:absolute;left:0;width:850px;padding-right:80px;top:760px;text-align:center;white-space:nowrap;
    font-weight:300;font-size:66px;color:var(--ink);letter-spacing:-1px}
  .leaf-border{position:absolute;left:0;top:842px;width:100%;height:132px;
    background:linear-gradient(180deg,rgba(108,184,79,0) 0%,#5fae4a 45%,#2f7d33 100%)}
  .band-bottom{position:absolute;left:0;top:974px;width:100%;height:120px;background:var(--green-dark);
    color:var(--white);font-weight:300;font-size:52px;display:flex;align-items:center;justify-content:center;letter-spacing:-.5px;white-space:nowrap}
  .claims{position:absolute;left:750px;top:70px;width:96px;text-align:center;color:var(--green-dark)}
  .claim{display:flex;flex-direction:column;align-items:center;margin-bottom:28px}
  .claim svg{width:44px;height:56px;stroke:var(--green-dark);fill:none;stroke-width:2.5;stroke-linecap:round;stroke-linejoin:round;margin-bottom:12px}
  .claim span{font-weight:600;font-size:22px;line-height:1.2;letter-spacing:-.3px;white-space:nowrap}
</style>
</head>
<body>
<main class="label">
  <div class="band-top"></div>
  <div class="count-tab"><div class="num">60</div><div class="unit">GUMMIES</div></div>
  <div class="leaf-spray" role="img" aria-label="Cluster of fresh green leaves"></div>

  <p class="brand">RT HALVORSEN'S</p>
  <h1 class="title title-main">MEADOW CRUNCH</h1>
  <p class="title title-sub">CHEWS™</p>

  <div class="blend-pill">SUPER GREENS BLEND FOR</div>
  <p class="benefit benefit-main">ENERGY, DIGESTION,</p>
  <p class="benefit benefit-sub">AND IMMUNE SUPPORT*</p>
  <p class="supplement">DIETARY SUPPLEMENT</p>

  <aside class="claims">
    <div class="claim">
      <svg viewBox="0 0 46 58"><path d="M8 6c20 10 10 36 30 46M38 6C18 16 28 42 8 52M14 16h18M12 28h22M14 40h18"/></svg>
      <span>Non<br>GMO</span>
    </div>
    <div class="claim">
      <svg viewBox="0 0 46 58"><path d="M30 18L8 54l30-28zM30 18l6-10M34 20l8-6M32 19l4-12"/></svg>
      <span>VEGAN<br>FRIENDLY</span>
    </div>
    <div class="claim">
      <svg viewBox="0 0 46 58"><path d="M23 54V24M23 54C8 44 8 20 23 4c15 16 15 40 0 50zM23 36l-8-8M23 30l8-8"/></svg>
      <span>PLANT<br>BASED</span>
    </div>
    <div class="claim">
      <svg viewBox="0 0 46 58"><path d="M16 16a6 6 0 1 0-6 8v0a6 6 0 1 0 6 8l14 0a6 6 0 1 0 6-8a6 6 0 1 0-6-8z"/></svg>
      <span>GELATIN<br>FREE</span>
    </div>
  </aside>

  <div class="leaf-border" role="img" aria-label="Row of green leaves along the lower edge"></div>
  <div class="band-bottom">RASPBERRY FLAVOR GUMMIES</div>
</main>
</body>
</html>
```